New Business Card Design Project

Use the flyer uploaded and website www.brightoakbuilders.com for inspiration.
List Our Services on Backside of business cards
Marcus Delling
Harborline Builders Inc.
Licensed General Contractors
858-471-6093

Contact Information for Business Card

Use the flyer uploaded and website www.brightoakbuilders.com for inspiration. List Our Services on Backside of business cards Marcus Delling Harborline Builders Inc. Licensed General Contractors 858-471-6093

```html
<!DOCTYPE html>
<html lang="en">
<head>
<meta charset="utf-8">
<title>Harborline Builders – Business Cards</title>
<link href="https://fonts.googleapis.com/css2?family=Roboto:wght@400;500;900&display=swap" rel="stylesheet">
<style>
  :root {
    --stage: #232323;
    --card: #26262b;
    --edge: #e3202a;
    --red: #ee2a2f;
    --blue: #4f7fd6;
    --white: #ffffff;
    --soft: #e6e6e8;
  }
  * { margin: 0; padding: 0; box-sizing: border-box; }
  html, body { width: 1200px; height: 780px; overflow: hidden; }
  body {
    background: var(--stage);
    font-family: "Roboto", Arial, sans-serif;
    color: var(--white);
    display: flex;
    align-items: center;
    justify-content: center;
    gap: 40px;
  }
  .card {
    position: relative;
    width: 540px;
    height: 310px;
    background: var(--card);
    border-radius: 24px;
    border-bottom: 5px solid var(--edge);
    box-shadow: 0 0 0 1px #1b1b1e, 0 14px 30px rgba(0,0,0,.55);
    overflow: hidden;
  }
  .brand {
    position: absolute;
    display: flex;
    align-items: center;
    gap: 9px;
    white-space: nowrap;
  }
  .brand-mark {
    width: 12px; height: 12px;
    border-radius: 50%;
    background: var(--white);
    flex: none;
  }
  .brand-name {
    font-weight: 400;
    font-size: 17px;
    letter-spacing: 1px;
    text-transform: uppercase;
    color: var(--white);
  }
  /* back side */
  .card-back .brand { left: 30px; top: 140px; }
  .services { position: absolute; left: 318px; top: 36px; }
  .services-guarantee {
    color: var(--red);
    font-weight: 900;
    font-size: 13px;
    line-height: 1.15;
    text-transform: uppercase;
  }
  .services-heading {
    color: var(--blue);
    font-weight: 900;
    font-size: 13px;
    text-transform: uppercase;
    margin: 2px 0 8px;
  }
  .service-list { list-style: none; }
  .service-list li {
    display: flex;
    align-items: center;
    gap: 7px;
    font-size: 11.5px;
    line-height: 20px;
    color: var(--soft);
    white-space: nowrap;
  }
  .tick { width: 13px; height: 13px; flex: none; }
  /* front side */
  .card-front .brand { left: 36px; top: 62px; }
  .person { position: absolute; right: 0; top: 118px; display: flex; align-items: stretch; }
  .person-text { text-align: right; padding-right: 10px; }
  .person-name {
    color: var(--red);
    font-weight: 900;
    font-size: 27px;
    text-transform: uppercase;
    line-height: 1;
  }
  .person-role { font-size: 12px; font-weight: 500; margin-top: 4px; }
  .person-bar { width: 22px; background: var(--red); }
  .contact { position: absolute; left: 36px; bottom: 26px; }
  .contact-company { font-size: 13px; font-weight: 500; margin-bottom: 10px; }
  .contact-line { display: flex; align-items: center; gap: 9px; font-size: 13px; line-height: 22px; }
  .contact-icon { width: 14px; height: 14px; flex: none; }
</style>
</head>
<body>

<section class="card card-back" aria-label="Business card back">
  <div class="brand">
    <span class="brand-mark"></span>
    <span class="brand-name">Harborline Builders</span>
  </div>
  <div class="services">
    <p class="services-guarantee">Our services are<br>100% guaranteed</p>
    <p class="services-heading">Specializing in:</p>
    <ul class="service-list">
      <li><svg class="tick" viewBox="0 0 14 14"><circle cx="7" cy="7" r="6" fill="none" stroke="#ee2a2f" stroke-width="1.3"/><path d="M4 7.2l2 2 4-4.4" fill="none" stroke="#ee2a2f" stroke-width="1.6"/></svg>Remodel: Kitchen &amp; Bath</li>
      <li><svg class="tick" viewBox="0 0 14 14"><circle cx="7" cy="7" r="6" fill="none" stroke="#ee2a2f" stroke-width="1.3"/><path d="M4 7.2l2 2 4-4.4" fill="none" stroke="#ee2a2f" stroke-width="1.6"/></svg>Painting: Interior &amp; Exterior</li>
      <li><svg class="tick" viewBox="0 0 14 14"><circle cx="7" cy="7" r="6" fill="none" stroke="#ee2a2f" stroke-width="1.3"/><path d="M4 7.2l2 2 4-4.4" fill="none" stroke="#ee2a2f" stroke-width="1.6"/></svg>Flooring: Carpet, Vinyl, Wood</li>
      <li><svg class="tick" viewBox="0 0 14 14"><circle cx="7" cy="7" r="6" fill="none" stroke="#ee2a2f" stroke-width="1.3"/><path d="M4 7.2l2 2 4-4.4" fill="none" stroke="#ee2a2f" stroke-width="1.6"/></svg>Window &amp; Door Replacement</li>
      <li><svg class="tick" viewBox="0 0 14 14"><circle cx="7" cy="7" r="6" fill="none" stroke="#ee2a2f" stroke-width="1.3"/><path d="M4 7.2l2 2 4-4.4" fill="none" stroke="#ee2a2f" stroke-width="1.6"/></svg>Plumbing: Repairs &amp; Upgrades</li>
      <li><svg class="tick" viewBox="0 0 14 14"><circle cx="7" cy="7" r="6" fill="none" stroke="#ee2a2f" stroke-width="1.3"/><path d="M4 7.2l2 2 4-4.4" fill="none" stroke="#ee2a2f" stroke-width="1.6"/></svg>Energy-Efficient Upgrades</li>
      <li><svg class="tick" viewBox="0 0 14 14"><circle cx="7" cy="7" r="6" fill="none" stroke="#ee2a2f" stroke-width="1.3"/><path d="M4 7.2l2 2 4-4.4" fill="none" stroke="#ee2a2f" stroke-width="1.6"/></svg>Deck &amp; Patio Construction</li>
      <li><svg class="tick" viewBox="0 0 14 14"><circle cx="7" cy="7" r="6" fill="none" stroke="#ee2a2f" stroke-width="1.3"/><path d="M4 7.2l2 2 4-4.4" fill="none" stroke="#ee2a2f" stroke-width="1.6"/></svg>Water &amp; Mold Damage</li>
      <li><svg class="tick" viewBox="0 0 14 14"><circle cx="7" cy="7" r="6" fill="none" stroke="#ee2a2f" stroke-width="1.3"/><path d="M4 7.2l2 2 4-4.4" fill="none" stroke="#ee2a2f" stroke-width="1.6"/></svg>Garage Renovation</li>
    </ul>
  </div>
</section>

<section class="card card-front" aria-label="Business card front">
  <div class="brand">
    <span class="brand-mark"></span>
    <span class="brand-name">Harborline Builders</span>
  </div>
  <div class="person">
    <div class="person-text">
      <p class="person-name">Marcus Delling</p>
      <p class="person-role">Licensed General Contractors</p>
    </div>
    <div class="person-bar"></div>
  </div>
  <div class="contact">
    <p class="contact-company">Harborline Builders Inc.</p>
    <p class="contact-line">
      <svg class="contact-icon" viewBox="0 0 24 24"><path fill="#ee2a2f" d="M6.6 10.8a15.1 15.1 0 006.6 6.6l2.2-2.2a1 1 0 011-.25 11.4 11.4 0 003.6.57 1 1 0 011 1V20a1 1 0 01-1 1A17 17 0 013 4a1 1 0 011-1h3.5a1 1 0 011 1c0 1.25.2 2.45.57 3.57a1 1 0 01-.25 1z"/></svg>
      858-471-6093
    </p>
    <p class="contact-line">
      <svg class="contact-icon" viewBox="0 0 24 24"><rect x="2" y="5" width="20" height="14" rx="2" fill="#ee2a2f"/><path d="M3 6l9 7 9-7" fill="none" stroke="#26262b" stroke-width="1.8"/></svg>
      info@brightoakbuilders.com
    </p>
    <p class="contact-line">
      <svg class="contact-icon" viewBox="0 0 24 24"><circle cx="12" cy="12" r="10" fill="#ee2a2f"/><path d="M2 12h20M12 2c3 3 3 17 0 20M12 2c-3 3-3 17 0 20" fill="none" stroke="#26262b" stroke-width="1.4"/></svg>
      www.brightoakbuilders.com
    </p>
  </div>
</section>

</body>
</html>
```